Business Card Design

We need a business card designed for a new company based in Melbourne called Kvt solutions. Kvt solutions provides management consulting specialising in the health and social services sector.

Kvt solutions offer a unique set of specialist skills │dealing with all levels of government │ unique communication skills│intimate knowledge of the health sector │solutions tailored to unique circumstances.

Kvt solutions takes on a select number of clients at any one time, this ensures that your organisation receives the attention required. On larger projects, Kvt solutions join up with other consultants to bring specialist skills to a project.
Updates

This is the first time I have used Pixel Harbor and thank you all for responding. The variation is amazing and makes it hard to decide. I have to ask some of my friends to give me their views. The response is fantastic. The one I pick will basically be the most visually appealing

Industry/Entity Type

Management Consulting

Contact Information for Business Card

Martin Oakes, Principal, Kvt solutions, 14 Wexcombe Ave, Larkdale VIC 3189, 0417 382 914, martino@kvtsolutions-example.com.au, www.kvtsolutions-example.com.au

```html
<!DOCTYPE html>
<html lang="en">
<head>
<meta charset="utf-8">
<title>Kvt solutions – Business Card</title>
<link rel="stylesheet" href="https://fonts.googleapis.com/css2?family=Open+Sans:wght@400;600;700&family=Roboto+Slab:wght@700&display=swap">
<style>
  :root {
    --brand-red: #c0172f;
    --brand-red-dark: #a8122a;
    --card-white: #ffffff;
    --ink: #1e1e1e;
    --backdrop: #e9e7e3;
  }
  * { box-sizing: border-box; margin: 0; padding: 0; }
  html, body {
    width: 1200px;
    height: 914px;
    overflow: hidden;
    background: var(--backdrop);
  }
  .canvas {
    position: relative;
    width: 1200px;
    height: 914px;
    display: flex;
    align-items: center;
    justify-content: center;
  }
  .business-card {
    position: relative;
    width: 1000px;
    height: 570px;
    background: var(--card-white);
    box-shadow: 0 6px 24px rgba(0,0,0,0.18);
    overflow: hidden;
    font-family: "Open Sans", Arial, sans-serif;
    color: var(--ink);
  }
  .brand-band {
    position: absolute;
    left: 0; top: 0;
    width: 100%;
    height: 222px;
    background: var(--brand-red);
  }
  .brand-name {
    position: absolute;
    left: 150px;
    top: 34px;
    font-family: "Open Sans", Arial, sans-serif;
    font-weight: 600;
    font-size: 98px;
    line-height: 1;
    letter-spacing: 1px;
    color: var(--card-white);
    white-space: nowrap;
  }
  .brand-tagline {
    position: absolute;
    right: 108px;
    top: 168px;
    font-family: "Roboto Slab", Georgia, serif;
    font-weight: 700;
    font-size: 21px;
    letter-spacing: 0.5px;
    text-transform: uppercase;
    color: var(--card-white);
    white-space: nowrap;
  }
  .contact-block {
    position: absolute;
    left: 230px;
    top: 258px;
    width: 640px;
    text-align: center;
  }
  .person-name {
    font-size: 32px;
    font-weight: 400;
    text-transform: uppercase;
    letter-spacing: 0.5px;
    line-height: 1.15;
  }
  .person-role {
    font-size: 25px;
    line-height: 1.2;
    margin-bottom: 12px;
  }
  .contact-line {
    font-size: 21px;
    line-height: 1.3;
    white-space: nowrap;
  }
  .pattern-band {
    position: absolute;
    left: 0; bottom: 0;
    width: 100%;
    height: 52px;
    background: linear-gradient(var(--brand-red), var(--brand-red-dark));
  }
</style>
</head>
<body>
  <main class="canvas">
    <article class="business-card">
      <header class="brand-band">
        <div class="brand-name">Kvt solutions</div>
        <div class="brand-tagline">Health &amp; Social Services Consulting</div>
      </header>

      <section class="contact-block">
        <h1 class="person-name">Martin Oakes</h1>
        <p class="person-role">Principal</p>
        <p class="contact-line">Kvt solutions, 14 Wexcombe Ave,</p>
        <p class="contact-line">Larkdale VIC 3189, 0417 382 914,</p>
        <p class="contact-line">martino@kvtsolutions-example.com.au , www.kvtsolutions-example.com.au</p>
      </section>

      <div class="pattern-band" role="img" aria-label="Red footer band with a repeating cross pattern"></div>
    </article>
  </main>
</body>
</html>
```